Flyer für Immobilienmakler
Zielgruppe
Wir, die Kessler Immobilien GmbH, vermitteln Häuser, Wohnungen und Grundstücke, unsere Zielgruppe sind Verkäufer und Kaufinteressenten aus der Region, Immobilien zur Vermittlung gesucht
Aufgabenstellung
Unverbindliche Ersteinschätzung, Ansprechpartner vor Ort, regionale Marktkenntnis. Max. Din A 5, Immobilien zur Vermittlung gesucht.
- Flyer nur zur Immobilienvermittlung

```html
<!DOCTYPE html>
<html lang="de">
<head>
<meta charset="utf-8">
<title>Kessler Immobilien – Flyer Immobilienvermittlung</title>
<link href="https://fonts.googleapis.com/css2?family=Barlow+Semi+Condensed:wght@300;400;600&family=Cabin:wght@400;500&display=swap" rel="stylesheet">
<style>
  :root{
    --bg:#d3d3d3;
    --paper:#ffffff;
    --purple:#6e58a1;
    --green:#13a37e;
    --ink:#222222;
    --text:#4a4a4a;
    --white:#ffffff;
  }
  *{box-sizing:border-box;margin:0;padding:0}
  html,body{width:1200px;height:1200px;overflow:hidden;background:var(--bg)}
  .flyer{position:absolute;left:200px;top:34px;width:800px;height:1131px;background:var(--paper);overflow:hidden;box-shadow:0 4px 12px rgba(0,0,0,.25);font-family:"Cabin",sans-serif;color:var(--text)}
  .hero-photo{position:absolute;left:483px;top:0;width:317px;height:672px;background:linear-gradient(160deg,#8a8f88 0%,#56654a 30%,#3f5233 60%,#4a4f45 100%)}
  .header{position:absolute;left:0;top:0;width:530px;height:156px;background:var(--purple)}
  .header h1{position:absolute;left:46px;top:38px;font-family:"Barlow Semi Condensed",sans-serif;font-weight:300;font-size:34px;line-height:42px;letter-spacing:2.2px;color:var(--white);white-space:nowrap}
  .brand{position:absolute;left:540px;top:82px;width:260px;text-align:center;font-family:"Cabin",sans-serif;font-size:14px;letter-spacing:.5px;color:var(--white)}
  .section-title{position:absolute;font-family:"Barlow Semi Condensed",sans-serif;font-weight:600;font-size:20.5px;color:var(--ink);white-space:nowrap}
  .bar{position:absolute;height:16px;background:var(--green)}
  .copy{position:absolute;font-size:14.3px;line-height:19px}
  .copy p+p{margin-top:10px}
  .service{margin-bottom:8px}
  .service h3{font-weight:400;font-size:15.5px;color:var(--ink);line-height:21px}
  .door-photo{position:absolute;left:0;top:672px;width:369px;height:459px;background:linear-gradient(90deg,#bcc8d4 0%,#cfd7de 50%,#e4e1da 75%,#e8ebe0 100%)}
  .info-panel{position:absolute;left:369px;top:672px;width:431px;height:352px;background:linear-gradient(90deg,#f6f6f2 0%,#ffffff 80%)}
  .checklist{list-style:none;font-size:15px;line-height:19px}
  .checklist li{position:relative;padding-left:23px;margin-bottom:5px}
  .checklist svg{position:absolute;left:0;top:4px}
  .contact{position:absolute;left:252px;top:1024px;width:548px;height:107px;background:var(--green);color:var(--white)}
  .contact h2{position:absolute;left:18px;top:15px;font-family:"Barlow Semi Condensed",sans-serif;font-weight:600;font-size:20px}
  .contact .rule{position:absolute;left:108px;top:27px;width:394px;height:1px;background:rgba(255,255,255,.7)}
  .contact .company{position:absolute;left:18px;top:58px;font-size:14.5px;line-height:18px}
  .contact .company strong{font-family:"Barlow Semi Condensed",sans-serif;font-weight:600;font-size:16px}
  .contact .lines{position:absolute;left:262px;top:57px;font-size:14.5px;line-height:21px}
  .contact .lines b{font-weight:500}
</style>
</head>
<body>
<div class="flyer">
  <div class="hero-photo" role="img" aria-label="Luftaufnahme eines Wohngebiets mit Einfamilienhäusern"></div>
  <div class="header">
    <h1>IHR REGIONALER PARTNER FÜR<br>IMMOBILIENVERMITTLUNG</h1>
  </div>
  <div class="brand">Kessler Immobilien GmbH</div>

  <div class="bar" style="left:0;top:189px;width:37px"></div>
  <h2 class="section-title" style="left:46px;top:183px">KOMPETENTE IMMOBILIENVERMITTLUNG VOR ORT</h2>
  <div class="copy" style="left:46px;top:222px;width:400px">
    <p>Die Kessler Immobilien GmbH mit Sitz in Lindach ist Ihr zuverlässiger Ansprechpartner beim Verkauf und Kauf von Häusern, Wohnungen und Grundstücken.</p>
    <p>Mit fundierter regionaler Marktkenntnis und persönlicher Betreuung begleiten wir Verkäufer und Kaufinteressenten aus der Region.</p>
  </div>

  <div class="bar" style="left:0;top:373px;width:37px"></div>
  <h2 class="section-title" style="left:46px;top:367px">UNSERE LEISTUNGEN</h2>
  <div class="copy" style="left:46px;top:405px;width:400px">
    <div class="service"><h3>Unverbindliche Ersteinschätzung</h3><p>Wir ermitteln kostenfrei und unverbindlich eine erste, marktgerechte Einschätzung des Werts Ihrer Immobilie – direkt vor Ort.</p></div>
    <div class="service"><h3>Immobilienverkauf</h3><p>Von der Präsentation bis zum Notartermin – wir sind Ihr kompetenter Partner für den erfolgreichen Verkauf Ihrer Immobilie.</p></div>
    <div class="service"><h3>Immobilienvermittlung</h3><p>Ob Haus, Wohnung oder Grundstück – wir kümmern uns zuverlässig um die Vermittlung an passende Kaufinteressenten aus der Region.</p></div>
  </div>

  <div class="door-photo" role="img" aria-label="Türgriff mit Schlüssel und Hausanhänger in hellem Raum"></div>
  <div class="info-panel"></div>

  <div class="bar" style="left:369px;top:731px;width:30px"></div>
  <h2 class="section-title" style="left:409px;top:725px">WARUM KESSLER IMMOBILIEN?</h2>
  <ul class="checklist" style="position:absolute;left:417px;top:760px;width:340px">
    <li><svg width="14" height="12" viewBox="0 0 14 12"><path d="M1 1l5 5-5 5M7 1l5 5-5 5" fill="none" stroke="#6e58a1" stroke-width="2.2"/></svg>Persönlicher Ansprechpartner vor Ort</li>
    <li><svg width="14" height="12" viewBox="0 0 14 12"><path d="M1 1l5 5-5 5M7 1l5 5-5 5" fill="none" stroke="#6e58a1" stroke-width="2.2"/></svg>Umfassende regionale Marktkenntnis</li>
    <li><svg width="14" height="12" viewBox="0 0 14 12"><path d="M1 1l5 5-5 5M7 1l5 5-5 5" fill="none" stroke="#6e58a1" stroke-width="2.2"/></svg>Unverbindliche Ersteinschätzung Ihrer Immobilie</li>
    <li><svg width="14" height="12" viewBox="0 0 14 12"><path d="M1 1l5 5-5 5M7 1l5 5-5 5" fill="none" stroke="#6e58a1" stroke-width="2.2"/></svg>Zuverlässiger Partner für Verkäufer und Kaufinteressenten</li>
  </ul>

  <div class="bar" style="left:369px;top:898px;width:30px"></div>
  <h2 class="section-title" style="left:407px;top:891px">IMMOBILIEN ZUR VERMITTLUNG GESUCHT</h2>
  <p class="copy" style="left:407px;top:927px;font-size:15px">Wir sind laufend auf der Suche nach:</p>
  <ul class="checklist" style="position:absolute;left:415px;top:953px;width:170px">
    <li><svg width="14" height="12" viewBox="0 0 14 12"><path d="M1 1l5 5-5 5M7 1l5 5-5 5" fill="none" stroke="#6e58a1" stroke-width="2.2"/></svg>Häusern</li>
    <li><svg width="14" height="12" viewBox="0 0 14 12"><path d="M1 1l5 5-5 5M7 1l5 5-5 5" fill="none" stroke="#6e58a1" stroke-width="2.2"/></svg>Wohnungen</li>
  </ul>
  <ul class="checklist" style="position:absolute;left:593px;top:953px;width:180px">
    <li><svg width="14" height="12" viewBox="0 0 14 12"><path d="M1 1l5 5-5 5M7 1l5 5-5 5" fill="none" stroke="#6e58a1" stroke-width="2.2"/></svg>Grundstücken</li>
    <li><svg width="14" height="12" viewBox="0 0 14 12"><path d="M1 1l5 5-5 5M7 1l5 5-5 5" fill="none" stroke="#6e58a1" stroke-width="2.2"/></svg>zum Kauf in der Region.</li>
  </ul>

  <div class="contact">
    <h2>KONTAKT</h2>
    <div class="rule"></div>
    <div class="company"><strong>KESSLER IMMOBILIEN GMBH</strong><br>Talweg 7 84390 Lindach</div>
    <div class="lines"><b>T</b>: +49 85 11 402380-0<br><b>E</b>: kontakt@kessler-lindach.de</div>
  </div>
</div>
</body>
</html>
```